Valmora Health a direct primary care practice needs a beautiful and customer friendly website

We need a website to showcase our new medical practice. We want to enhance the customer experience and make it easy to navigate to the desired page by placing pillar pages on the home screen. the website needs to be clean and bright.

Target Market(s)

Uninsured, Small businesses that can't afford to offer employees insurance.

Industry/Entity Type

Healthcare

Coding

Coded - Design and coding required

Font styles to use
Serif
Sans Serif

Colors
0592cd
3377b5
0355a3
9bcb3c
acd136

Requirements
Must have
• Must be user friendly, must have pillar pages to help boost SEO ranking, clean and bright, must be close to the in colors to the attached logo.

Content will be very similar to www.quillbrookhealth.example
Nice to have
• Clean and easy to read font

```html
<!DOCTYPE html>
<html lang="en">
<head>
<meta charset="utf-8">
<title>Valmora Health</title>
<link href="https://fonts.googleapis.com/css2?family=Libre+Baskerville:wght@400;700&family=Poppins:ital,wght@0,300;0,400;0,500;1,300&display=swap" rel="stylesheet">
<style>
:root{
  --navy:#0b0a47;
  --navy-deep:#06053a;
  --green:#06923a;
  --green-text:#16773c;
  --blue:#3a66d0;
  --grey-bg:#f4f4f4;
  --text:#555;
  --dark:#111;
  --serif:'Libre Baskerville', Georgia, serif;
  --sans:'Poppins', Arial, sans-serif;
}
*{box-sizing:border-box;margin:0;padding:0}
html,body{width:1200px;height:3735px;overflow:hidden;background:#fff}
body{position:relative;font-family:var(--sans);color:var(--text)}
.abs{position:absolute}
.hero-photo{left:0;top:0;width:1200px;height:607px;background:linear-gradient(100deg,#c9a48b 0%,#e7d2c4 35%,#d9cfc8 60%,#b9b3ad 100%)}
.nav{left:145px;top:22px;width:904px;height:77px;background:#fff;border-left:3px solid var(--navy);border-bottom:4px solid var(--navy);display:flex;align-items:center}
.brand{margin-left:24px;width:220px;display:flex;align-items:center;gap:10px}
.brand-mark{width:14px;height:14px;border-radius:50%;background:var(--green);flex:none}
.brand-name{font-family:var(--sans);font-weight:500;font-size:21px;color:var(--navy)}
.menu{display:flex;gap:24px;margin-left:52px;font-size:11px;color:#222;text-transform:uppercase}
.menu .active{position:relative}
.menu .active::before{content:"";position:absolute;left:50%;top:-30px;width:2px;height:18px;background:var(--navy)}
.hero-title{right:63px;top:280px;text-align:right;font-family:var(--serif);font-weight:700;font-size:52px;line-height:68px;color:#0a0a0a;text-shadow:2px 3px 4px rgba(255,255,255,.6)}
.btn{display:inline-block;font-family:var(--sans);font-weight:500;font-size:14px;color:#fff;text-transform:uppercase;text-align:center;border-radius:4px}
.hero-btn{left:994px;top:464px;width:138px;height:35px;line-height:35px;background:var(--green)}
.features{left:0;top:607px;width:899px;height:149px;background:var(--navy-deep)}
.feature{top:607px;height:149px;width:210px;border-left:1px solid #34336a;padding:24px 16px;color:#fff}
.feature.raised{top:599px;height:165px;background:var(--navy);box-shadow:0 0 8px rgba(0,0,0,.3)}
.feature h3{display:flex;align-items:center;gap:8px;font-weight:400;font-size:17px;margin-bottom:12px}
.ficon{width:42px;height:42px;border-radius:50%;background:#fff;display:flex;align-items:center;justify-content:center;flex:none}
.feature p{font-size:11.5px;line-height:19px;max-width:165px}
.feature .phone{font-size:22px;margin-top:4px;max-width:none}
.about-photo{left:93px;top:848px;width:458px;height:358px;background:linear-gradient(110deg,#d8b8a6,#efe4da 55%,#9b9a96)}
.eyebrow{font-family:var(--serif);font-size:14px;color:var(--green-text);text-transform:uppercase}
.h2{font-family:var(--serif);font-weight:700;font-size:23px;line-height:30px;color:var(--dark)}
.para{font-size:12px;line-height:19.5px;color:#666}
.checks{left:627px;top:1088px;display:grid;grid-template-columns:180px 180px;row-gap:11px;font-size:12.5px;color:#666}
.checks div{display:flex;align-items:center;gap:14px}
.services-btn{left:1011px;top:1346px;width:128px;height:36px;line-height:36px;background:var(--navy);font-size:14px}
.grid{left:59px;top:1443px;width:1080px;height:599px;display:grid;grid-template-columns:354px 383px 343px;grid-template-rows:299px 300px;background:var(--grey-bg)}
.card{padding:44px 0 0 46px;border-right:1px solid var(--navy);border-bottom:1px solid var(--navy)}
.card:nth-child(3n){border-right:none}
.card:nth-child(n+4){border-bottom:none}
.card h3{display:flex;align-items:center;gap:20px;font-weight:400;font-size:18px;color:var(--navy);margin-bottom:20px}
.card .sicon{width:60px;height:60px;border-radius:50%;display:flex;align-items:center;justify-content:center;flex:none}
.sicon.blue{background:linear-gradient(135deg,#3b5bd6,#0d1a7a)}
.sicon.green{background:linear-gradient(135deg,#0aa34a,#05702b)}
.card h3.g{color:var(--green-text)}
.card p{font-size:12px;line-height:19.5px;color:#555;width:270px}
.more{margin-top:26px;display:flex;align-items:center;gap:10px;font-size:14px;font-weight:500;color:var(--navy)}
.more.g{color:var(--green-text)}
.band{left:0;top:2178px;width:1200px;height:539px;background:linear-gradient(90deg,#070642 0%,#1d2f9a 50%,#2e66f5 100%)}
.cta{left:196px;top:2147px;width:811px;height:115px;background:#fff;padding:4px;border-radius:3px}
.cta-left{left:4px;top:4px;width:440px;height:107px;background:var(--blue);padding:18px 24px;font-family:var(--serif);font-weight:700;font-size:22px;line-height:40px;color:#fff}
.cta-right{left:416px;top:4px;width:391px;height:107px;background:var(--green);border-radius:60px 0 0 60px;display:flex;align-items:center;gap:40px;padding-left:40px;color:#fff}
.cta-right .pc{width:48px;height:48px;border-radius:50%;background:#fff;display:flex;align-items:center;justify-content:center}
.cta-right .lbl{font-family:var(--serif);font-size:22px}
.cta-right .num{font-size:22px;margin-top:6px}
.fb{left:0;width:1200px;text-align:center;color:#fff}
.avatar{border-radius:50%;border:2px solid #fff;background:linear-gradient(135deg,#c8b3a2,#6e7e9e)}
.field{left:59px;width:338px;height:35px;border:1px solid #bbb;border-radius:3px;padding:8px 10px;font-size:11.5px;color:#555}
.map-photo{left:607px;top:2807px;width:451px;height:449px;background:linear-gradient(135deg,#dfe7ea,#c6d4d8 50%,#8a9aa2)}
.map-card{left:659px;top:2905px;width:344px;height:199px;background:#fff;opacity:.96}
.map-area{left:663px;top:2909px;width:185px;height:191px;background:linear-gradient(135deg,#eef0f3,#e2e6ec)}
.footer{left:0;top:3350px;width:1200px;height:332px;background:linear-gradient(90deg,#070642 0%,#1c2c95 55%,#2b5fe6 100%);color:#fff}
.footer-brand{left:61px;top:100px;display:flex;align-items:center;gap:10px;font-family:var(--sans);font-weight:500;font-size:25px;color:#fff}
.footer-brand .brand-mark{background:#fff}
.fcol h4{font-weight:400;font-size:18px;margin-bottom:14px}
.fcol li{list-style:none;font-size:12px;line-height:27px;color:#cfd5f5}
.copy{left:0;top:3682px;width:1200px;height:53px;background:var(--green);color:#fff;font-size:12px;text-align:center;line-height:53px}
</style>
</head>
<body>

<div class="abs hero-photo" role="img" aria-label="Photo of a smiling mother and daughter giving a high five to a doctor"></div>
<header class="abs nav">
  <div class="brand"><span class="brand-mark"></span><span class="brand-name">Valmora Health</span></div>
  <nav class="menu"><span class="active">Home</span><span>About</span><span>Services</span><span>Employers</span><span>Pricing</span><span>FAQ</span><span>Contact Us</span><span>Blog</span></nav>
</header>
<h1 class="abs hero-title">FIND THE CARE<br>YOU NEED</h1>
<a class="abs btn hero-btn">Contact Us</a>

<div class="abs features"></div>
<div class="abs feature" style="left:59px"><h3><span class="ficon"><svg width="24" height="24" viewBox="0 0 24 24"><circle cx="12" cy="8" r="5" fill="none" stroke="#0d1a7a" stroke-width="2"/><path d="M3 20h18" stroke="#06923a" stroke-width="2"/></svg></span>Benefits</h3><p>Lorem Ipsum is simply dummy text of the printing</p></div>
<div class="abs feature raised" style="left:270px"><h3><span class="ficon"><svg width="24" height="24" viewBox="0 0 24 24"><circle cx="10" cy="10" r="7" fill="none" stroke="#06923a" stroke-width="2"/><text x="10" y="14" font-size="10" text-anchor="middle" fill="#0d1a7a">?</text></svg></span>Questions?</h3><p>Lorem Ipsum is simply dummy text of the printing</p></div>
<div class="abs feature" style="left:480px"><h3><span class="ficon"><svg width="24" height="24" viewBox="0 0 24 24"><circle cx="12" cy="12" r="9" fill="none" stroke="#06923a" stroke-width="2"/><path d="M12 7v5l3 3" stroke="#0d1a7a" stroke-width="2" fill="none"/></svg></span>Office Hours</h3><p>MWF 9:00 AM – 5:00 PM<br>T/Th 8:00 AM – 4:00 PM</p></div>
<div class="abs feature" style="left:690px"><h3><span class="ficon"><svg width="22" height="22" viewBox="0 0 24 24"><path d="M6 3l4 4-2 3c1 2 3 4 5 5l3-2 4 4-3 3C10 20 4 14 3 6z" fill="#06923a"/></svg></span>Call Us</h3><p class="phone">555 014 2290</p></div>

<div class="abs about-photo" role="img" aria-label="Photo of a child and mother greeting a doctor in a clinic"></div>
<div class="abs eyebrow" style="left:632px;top:853px">About Us</div>
<h2 class="abs h2" style="left:632px;top:884px;width:475px">There are many variations of passages of Lorem Ipsum available, but the majority have suffered</h2>
<p class="abs para" style="left:632px;top:992px;width:400px">Lorem ipsum dolor sit amet, consectetur adipiscing elit, sed do eiusmod tempor incididunt ut labore et dolore magna aliqua. Ut enim ad minim veniam, quis nostrud exercitation ullamco laboris nisi ut aliquip ex ea commodo consequat.</p>
<div class="abs checks">
  <div><svg width="16" height="12"><path d="M1 6l5 5 9-10" stroke="#0b0a47" stroke-width="2" fill="none"/></svg>Complete</div>
  <div><svg width="16" height="12"><path d="M1 6l5 5 9-10" stroke="#0b0a47" stroke-width="2" fill="none"/></svg>Complete</div>
  <div><svg width="16" height="12"><path d="M1 6l5 5 9-10" stroke="#0b0a47" stroke-width="2" fill="none"/></svg>Cosmetic</div>
  <div><svg width="16" height="12"><path d="M1 6l5 5 9-10" stroke="#0b0a47" stroke-width="2" fill="none"/></svg>Cosmetic</div>
  <div><svg width="16" height="12"><path d="M1 6l5 5 9-10" stroke="#0b0a47" stroke-width="2" fill="none"/></svg>Dental x- ray</div>
  <div><svg width="16" height="12"><path d="M1 6l5 5 9-10" stroke="#0b0a47" stroke-width="2" fill="none"/></svg>Dental x- ray</div>
</div>

<div class="abs eyebrow" style="left:96px;top:1300px">About Us</div>
<h2 class="abs h2" style="left:96px;top:1330px">There are many variations of passages of Lorem</h2>
<p class="abs para" style="left:96px;top:1376px;width:400px">Lorem ipsum dolor sit amet, consectetur adipiscing elit, sed do eiusmod tempor incididunt ut labore et dolore magna aliqua.</p>
<a class="abs btn services-btn">Contact Us</a>

<section class="abs grid">
  <div class="card"><h3 class="g"><span class="sicon blue"><svg width="28" height="28" viewBox="0 0 24 24"><rect x="3" y="4" width="18" height="16" rx="2" fill="none" stroke="#fff" stroke-width="1.5"/><path d="M9 12h6M12 9v6" stroke="#fff" stroke-width="1.5"/></svg></span>General Health Visits</h3><p>Lorem Ipsum is simply dummy text of the printing and typesetting industry. standard dummy text ever since the 1500s, when an unknown printer took</p><div class="more">LEARN MORE <svg width="26" height="10"><path d="M0 5h24M19 1l5 4-5 4" stroke="#0b0a47" stroke-width="1.5" fill="none"/></svg></div></div>
  <div class="card"><h3><span class="sicon green"><svg width="28" height="28" viewBox="0 0 24 24"><path d="M3 18h18M5 18V8M5 13h14v5" stroke="#fff" stroke-width="1.5" fill="none"/></svg></span>Physical Exams</h3><p>Lorem Ipsum is simply dummy text of the printing and typesetting industry. standard dummy text ever since the 1500s, when an unknown printer took</p><div class="more g">LEARN MORE <svg width="26" height="10"><path d="M0 5h24M19 1l5 4-5 4" stroke="#16773c" stroke-width="1.5" fill="none"/></svg></div></div>
  <div class="card"><h3 class="g"><span class="sicon blue"><svg width="28" height="28" viewBox="0 0 24 24"><rect x="4" y="4" width="16" height="16" rx="2" fill="none" stroke="#fff" stroke-width="1.5"/><path d="M8 12l3 3 5-6" stroke="#fff" stroke-width="1.5" fill="none"/></svg></span>Specialized Treatments</h3><p>Lorem Ipsum is simply dummy text of the printing and typesetting industry. standard dummy text ever since the 1500s, when an unknown printer took</p><div class="more">LEARN MORE <svg width="26" height="10"><path d="M0 5h24M19 1l5 4-5 4" stroke="#0b0a47" stroke-width="1.5" fill="none"/></svg></div></div>
  <div class="card"><h3><span class="sicon green"><svg width="28" height="28" viewBox="0 0 24 24"><circle cx="10" cy="12" r="6" fill="none" stroke="#fff" stroke-width="1.5"/><path d="M19 4v12" stroke="#fff" stroke-width="1.5"/></svg></span>Vaccinations</h3><p>Lorem Ipsum is simply dummy text of the printing and typesetting industry. standard dummy text ever since the 1500s, when an unknown printer took</p><div class="more g">LEARN MORE <svg width="26" height="10"><path d="M0 5h24M19 1l5 4-5 4" stroke="#16773c" stroke-width="1.5" fill="none"/></svg></div></div>
  <div class="card" style="padding-top:36px"><h3 class="g"><span class="sicon blue"><svg width="28" height="28" viewBox="0 0 24 24"><rect x="3" y="5" width="18" height="12" rx="1" fill="none" stroke="#fff" stroke-width="1.5"/><path d="M8 20h8" stroke="#fff" stroke-width="1.5"/></svg></span>Telemedicine</h3><p>Lorem Ipsum is simply dummy text of the printing and typesetting industry. standard dummy text ever since the 1500s, when an unknown printer took</p><div class="more">LEARN MORE <svg width="26" height="10"><path d="M0 5h24M19 1l5 4-5 4" stroke="#0b0a47" stroke-width="1.5" fill="none"/></svg></div></div>
  <div class="card" style="padding-left:53px"><h3><span class="sicon green"><svg width="28" height="28" viewBox="0 0 24 24"><rect x="4" y="6" width="16" height="12" rx="2" fill="none" stroke="#fff" stroke-width="1.5"/><circle cx="12" cy="12" r="3" fill="none" stroke="#fff" stroke-width="1.5"/></svg></span>Medical Imaging</h3><p>Lorem Ipsum is simply dummy text of the printing and typesetting industry. standard dummy text ever since the 1500s, when an unknown printer took</p><div class="more g">LEARN MORE <svg width="26" height="10"><path d="M0 5h24M19 1l5 4-5 4" stroke="#16773c" stroke-width="1.5" fill="none"/></svg></div></div>
</section>

<div class="abs band"></div>
<div class="abs cta">
  <div class="abs cta-left">Get a Free Checkup From<br>ValmoraHealth</div>
  <div class="abs cta-right"><span class="pc"><svg width="26" height="26" viewBox="0 0 24 24"><path d="M6 3l4 4-2 3c1 2 3 4 5 5l3-2 4 4-3 3C10 20 4 14 3 6z" fill="#3a66d0"/></svg></span><div><div class="lbl">Call Us</div><div class="num">555 014 2290</div></div></div>
</div>
<div class="abs fb" style="top:2340px;font-family:var(--serif);font-size:14px">OUR FEEDBACK</div>
<div class="abs fb" style="top:2370px;font-family:var(--serif);font-weight:700;font-size:23px">What client says about us</div>
<div class="abs fb" style="top:2412px;font-family:var(--serif);font-size:80px;line-height:80px;color:#5571c9">&ldquo;</div>
<p class="abs fb" style="top:2484px;left:280px;width:640px;font-style:italic;font-weight:300;font-size:14px;line-height:21px">Lorem ipsum dolor sit amet, consectetur adipiscing elit, sed do eiusmod tempor incididunt ut labore et dolore magna aliqua. Ut enim ad minim veniam, quis nostrud exercitation ullamco laboris nisi ut aliquip ex ea commodo consequat.</p>
<svg class="abs" style="left:132px;top:2495px" width="20" height="30"><path d="M17 2L4 15l13 13" stroke="#fff" stroke-width="2" fill="none"/></svg>
<svg class="abs" style="left:1048px;top:2495px" width="20" height="30"><path d="M3 2l13 13L3 28" stroke="#fff" stroke-width="2" fill="none"/></svg>
<div class="abs avatar" style="left:430px;top:2589px;width:52px;height:52px" role="img" aria-label="Client portrait"></div>
<div class="abs avatar" style="left:497px;top:2589px;width:52px;height:52px" role="img" aria-label="Client portrait"></div>
<div class="abs avatar" style="left:566px;top:2581px;width:67px;height:67px" role="img" aria-label="Client portrait"></div>
<div class="abs avatar" style="left:649px;top:2589px;width:52px;height:52px" role="img" aria-label="Client portrait"></div>
<div class="abs avatar" style="left:717px;top:2589px;width:52px;height:52px" role="img" aria-label="Client portrait"></div>

<div class="abs eyebrow" style="left:61px;top:2836px">Contact Us</div>
<h2 class="abs h2" style="left:61px;top:2866px">Get In Touch With Us</h2>
<div class="abs field" style="top:2921px">Name:</div>
<div class="abs field" style="top:2969px">Email:</div>
<div class="abs field" style="top:3018px">subject:</div>
<div class="abs field" style="top:3066px;height:67px">Message:</div>
<a class="abs btn" style="left:59px;top:3157px;width:128px;height:35px;line-height:35px;background:var(--navy);font-size:13px">Submit Now</a>
<div class="abs map-photo" role="img" aria-label="Photo of a doctor consulting a patient"></div>
<div class="abs map-card"></div>
<div class="abs map-area" role="img" aria-label="Street map showing the clinic location"></div>
<div class="abs" style="left:866px;top:2932px;font-family:var(--serif);font-size:14px;color:#222">VALMORAHEALTH</div>
<p class="abs" style="left:866px;top:2962px;width:120px;font-size:12px;line-height:19px;color:#666">101 Lorem Ipsum is dummy Text industies</p>
<div class="abs" style="left:876px;top:3078px;display:flex;gap:10px;align-items:center;font-size:12px;color:var(--navy)"><svg width="16" height="16" viewBox="0 0 16 16"><path d="M15 1L1 7l6 2 2 6z" fill="#2e68f7"/></svg>Get Direction</div>

<footer class="abs footer">
  <div class="abs footer-brand"><span class="brand-mark"></span>Valmora Health</div>
  <p class="abs" style="left:61px;top:167px;width:235px;font-size:12px;line-height:19.5px;color:#d8dcf5">Lorem Ipsum is simply dummy text of the printing and typesetting industry. Lorem Ipsum has been the industry's</p>
  <div class="abs fcol" style="left:338px;top:64px"><h4>Site Map</h4><ul><li>- Home</li><li>- About Us</li><li>- Services</li><li>- Employers</li><li>- Pricing</li><li>- FAQ</li><li>- Contact Us</li></ul></div>
  <div class="abs fcol" style="left:613px;top:64px"><h4>Site Map</h4>
    <div style="display:flex;gap:14px;font-size:12px;line-height:19px;color:#cfd5f5;width:240px"><svg width="16" height="20" viewBox="0 0 16 20" style="flex:none"><path d="M8 1a6 6 0 0 0-6 6c0 5 6 12 6 12s6-7 6-12a6 6 0 0 0-6-6z" fill="none" stroke="#2fb34a" stroke-width="1.5"/><circle cx="8" cy="7" r="2" fill="#2fb34a"/></svg>Lorem Ipsum is simply dummy text of the printing</div>
    <div style="display:flex;gap:14px;font-size:12px;color:#cfd5f5;margin-top:26px"><svg width="16" height="16" viewBox="0 0 24 24"><path d="M6 3l4 4-2 3c1 2 3 4 5 5l3-2 4 4-3 3C10 20 4 14 3 6z" fill="#2fb34a"/></svg>555 014 2290</div>
    <div style="display:flex;gap:14px;font-size:12px;color:#cfd5f5;margin-top:34px"><svg width="18" height="14" viewBox="0 0 18 14"><rect x="1" y="1" width="16" height="12" fill="none" stroke="#2fb34a" stroke-width="1.5"/><path d="M1 1l8 7 8-7" stroke="#2fb34a" stroke-width="1.5" fill="none"/></svg>info@valmorahealth.example</div>
  </div>
  <div class="abs fcol" style="left:888px;top:64px"><h4>Support</h4><ul><li>- Privacy Policy</li><li>- Terms &amp; Condition</li><li>- Support</li><li>- About</li><li>- News</li></ul></div>
</footer>
<div class="abs copy">©2021 valmorahealth.example - All Right Reserved</div>

</body>
</html>
```